KDWB Business Card

Looking for a business card design to incorporate our branding. We want to only use the colors listing in the Branding Package (attached).
Updates

Target Market(s)

People who need their phone or device fixed.

Industry/Entity Type

Electronics

Contact Information for Business Card

Please use:

Brightwick Gadget Clinic LLC
4810 E Harlow Ridge Rd
Suite 417
San Antonio, TX 78163

Marcus Delgrove, Store Manager

(210) 555-0147

Requirements
Must have
• Must include the colors that are contained within the Branding Package PDF file.

```html
<!DOCTYPE html>
<html lang="en">
<head>
<meta charset="utf-8">
<title>Brightwick Gadget Clinic — Business Card</title>
<link rel="stylesheet" href="https://fonts.googleapis.com/css2?family=Source+Sans+3:wght@400;600&display=swap">
<style>
  :root {
    --stage: #0a0a0a;
    --paper: #f2f2f2;
    --brand-orange: #ff5000;
    --ink: #2b2b2b;
    --white: #ffffff;
  }
  * { box-sizing: border-box; margin: 0; padding: 0; }
  html, body { width: 1200px; height: 900px; overflow: hidden; }
  body {
    background: var(--stage);
    font-family: "Source Sans 3", "Myriad Pro", Arial, sans-serif;
    position: relative;
  }
  .card {
    position: absolute;
    top: 170px;
    width: 347px;
    height: 561px;
  }
  .card--front { left: 259px; background: var(--paper); }
  .card--back { left: 631px; background: var(--brand-orange); }

  .brand {
    position: absolute;
    left: 37px;
    top: 141px;
    display: flex;
    align-items: center;
    gap: 12px;
  }
  .brand__square {
    width: 57px;
    height: 57px;
    border-radius: 8px;
    background: var(--brand-orange);
  }
  .brand__name {
    color: var(--brand-orange);
    font-size: 23px;
    font-weight: 400;
    line-height: 1;
  }

  .contact {
    position: absolute;
    left: 0;
    right: 0;
    top: 345px;
    text-align: center;
    color: var(--ink);
  }
  .contact__name {
    color: var(--brand-orange);
    font-size: 21px;
    font-weight: 600;
    letter-spacing: 0.6px;
    line-height: 1;
  }
  .contact__role {
    font-size: 15px;
    margin-top: 5px;
  }
  .contact__rule {
    width: 171px;
    height: 1px;
    background: var(--brand-orange);
    margin: 9px auto 0;
  }
  .contact__phone {
    margin-top: 16px;
    font-size: 15px;
    display: flex;
    justify-content: center;
    align-items: center;
    gap: 6px;
  }
  .contact__phone svg { width: 19px; height: 19px; fill: var(--brand-orange); }
  .contact__company {
    margin-top: 18px;
    color: var(--brand-orange);
    font-size: 15px;
    text-transform: uppercase;
  }
  .contact__address {
    font-size: 15.5px;
    line-height: 20px;
    margin-top: 1px;
  }

  .back__square {
    position: absolute;
    left: 93px;
    top: 200px;
    width: 162px;
    height: 161px;
    border-radius: 30px;
    background: var(--white);
  }
</style>
</head>
<body>
  <section class="card card--front">
    <div class="brand">
      <div class="brand__square"></div>
      <span class="brand__name">Brightwick Gadget Clinic</span>
    </div>

    <div class="contact">
      <p class="contact__name">MARCUS DELGROVE</p>
      <p class="contact__role">Store Manager</p>
      <div class="contact__rule"></div>
      <p class="contact__phone">
        <svg viewBox="0 0 24 24" aria-hidden="true"><path d="M6.6 10.8c1.4 2.8 3.8 5.1 6.6 6.6l2.2-2.2c.3-.3.7-.4 1-.2 1.1.4 2.3.6 3.6.6.6 0 1 .4 1 1V20c0 .6-.4 1-1 1C10.6 21 3 13.4 3 4c0-.6.4-1 1-1h3.5c.6 0 1 .4 1 1 0 1.3.2 2.5.6 3.6.1.3 0 .7-.2 1l-2.3 2.2z"/></svg>
        (210) 555-0147
      </p>
      <p class="contact__company">Brightwick Gadget Clinic LLC</p>
      <p class="contact__address">4810 E Harlow Ridge Rd<br>Suite 417 San Antonio, TX 78163</p>
    </div>
  </section>

  <section class="card card--back">
    <div class="back__square"></div>
  </section>
</body>
</html>
```